business card

Business card for new business.
Red and black corporate colors.
Card can have an Indsutrial feel to it. Feel free to add Rust, Bolted steel, or graphics as you see fit. We provide highly specialized services to the below mentioned industries.
Keep information out of corners so that if I want I can choose rounded corners.
Information
- front. name - title - phone - email
- Rear
Pipelines - Transit - Civil Works - Quarrying - Power
Harlow Bay - Pinecrest - Fort Ashby - Red Hollow - Westmere

```html
<!DOCTYPE html>
<html lang="en">
<head>
<meta charset="utf-8">
<title>Girderline business card</title>
<link rel="stylesheet" href="https://fonts.googleapis.com/css2?family=Roboto:wght@400;500;900&display=swap">
<style>
  :root {
    --bg: #e9e8e6;
    --card-white: #ffffff;
    --card-grey: #7f7f82;
    --brand-red: #e31e24;
    --ink-grey: #6b6b6e;
    --ink-dark: #4a4a4d;
    --white: #ffffff;
  }
  * { margin: 0; padding: 0; box-sizing: border-box; }
  html, body {
    width: 1200px; height: 930px; overflow: hidden;
    background: var(--bg);
    font-family: "Roboto", Arial, sans-serif;
  }
  .stage { position: relative; width: 1200px; height: 930px; }

  .card {
    position: absolute;
    width: 640px; height: 366px;
    border-radius: 18px;
    box-shadow: 0 6px 18px rgba(0,0,0,.18);
    overflow: hidden;
  }

  /* Rear */
  .card--rear { left: 80px; top: 70px; background: var(--card-grey); color: var(--white); }
  .rear-brand {
    position: absolute; left: 0; right: 0; top: 120px;
    display: flex; justify-content: center; align-items: center; gap: 16px;
  }
  .brand-square { width: 26px; height: 26px; background: currentColor; }
  .brand-name {
    font-weight: 900; font-size: 64px; letter-spacing: 1px; line-height: 1;
    white-space: nowrap;
  }
  .rear-lines {
    position: absolute; left: 0; right: 0; top: 250px;
    text-align: center; font-size: 15.5px; line-height: 1.55; font-weight: 400;
  }

  /* Front */
  .card--front { left: 480px; top: 494px; background: var(--card-white); }
  .front-brand {
    position: absolute; left: 50px; top: 158px;
    display: flex; align-items: center; gap: 12px;
    color: var(--ink-dark);
  }
  .front-brand .brand-square { width: 20px; height: 20px; background: var(--brand-red); }
  .front-brand .brand-name { font-size: 46px; color: var(--ink-dark); }
  .divider {
    position: absolute; left: 372px; top: 96px; width: 2px; height: 174px;
    background: var(--brand-red);
  }
  .contact { position: absolute; left: 396px; top: 86px; color: var(--ink-grey); }
  .contact__name {
    color: var(--brand-red); font-weight: 500; font-size: 22px; letter-spacing: .3px;
    text-transform: uppercase;
  }
  .contact__title { font-size: 15px; margin: 2px 0 8px; }
  .contact__line { font-size: 15px; line-height: 1.45; }
  .contact__row { display: flex; align-items: center; gap: 8px; font-size: 15px; line-height: 1.5; }
  .contact__row svg { width: 13px; height: 13px; flex: none; }
  .accent { color: var(--brand-red); }
</style>
</head>
<body>
<main class="stage">

  <section class="card card--rear" aria-label="Card back">
    <div class="rear-brand">
      <span class="brand-square" aria-hidden="true"></span>
      <span class="brand-name">GIRDERLINE</span>
    </div>
    <p class="rear-lines">
      Pipelines - Transit - Civil Works - Quarrying - Power<br>
      Harlow Bay - Pinecrest - Fort Ashby - Red Hollow - Westmere
    </p>
  </section>

  <section class="card card--front" aria-label="Card front">
    <div class="front-brand">
      <span class="brand-square" aria-hidden="true"></span>
      <span class="brand-name">GIRDERLINE</span>
    </div>
    <div class="divider" aria-hidden="true"></div>
    <div class="contact">
      <p class="contact__name">Daniel Harrow</p>
      <p class="contact__title">Director</p>
      <p class="contact__line">2290 Ridgeway Ave.</p>
      <p class="contact__line">Denver, CO 80205</p>
      <p class="contact__row">
        <svg viewBox="0 0 16 16" aria-hidden="true"><path fill="#e31e24" d="M3.6 1.5l2.2 2.6-1.3 1.6c.9 2 2.5 3.6 4.6 4.6l1.6-1.3 2.6 2.2-1.4 2.3C7 13.3 2.7 9 1.3 3z"/></svg>
        +1 303 555-0147
      </p>
      <p class="contact__row">
        <svg viewBox="0 0 16 16" aria-hidden="true"><rect x="1.5" y="3.5" width="13" height="9" fill="none" stroke="#e31e24" stroke-width="1.6"/><path d="M1.5 3.5L8 9l6.5-5.5" fill="none" stroke="#e31e24" stroke-width="1.6"/></svg>
        info@girderline.com
      </p>
      <p class="contact__row">
        <svg viewBox="0 0 16 16" aria-hidden="true"><circle cx="8" cy="8" r="6.3" fill="none" stroke="#e31e24" stroke-width="1.4"/><path d="M1.7 8h12.6M8 1.7c-3 3.4-3 9.2 0 12.6M8 1.7c3 3.4 3 9.2 0 12.6" fill="none" stroke="#e31e24" stroke-width="1.2"/></svg>
        <span>www.<span class="accent">girderline</span>.com</span>
      </p>
    </div>
  </section>

</main>
</body>
</html>
```